Stylish Business Cards Wanted

- DOUBLE SIDED Design Required -

High end, edgy cards for a corporate and personal stylist. Must include logo,
Name: Belinda Harwick
Title: Director and Stylist
telephone : +61 8 7142 5809
email: belinda@theloombriefing.example
website: theloombriefing.example
Tag: Corporate Workwear & Uniform Specialist | Personal Stylist
Would like nice icons for telephone, email, website

Target Market(s)

Businesses wanting stylish uniforms, people wanting stylish wardrobes

Industry/Entity Type

Corporate Workwear Stylist

Contact Information for Business Card

I would like black, white and gold foiling incorporated in the design - possibly a touch of the other colours on my branding guide attached Name: Belinda Harwick Title: Director and Stylist telephone : +61 8 7142 5809 email: belinda@theloombriefing.example website: theloombriefing.example Tag: Corporate Workwear & Uniform Specialist | Personal Stylist Would like nice icons for telephone, email, website

Font styles to use
Other font styles liked:
• Raleway

Colors

Designer to choose colors to be used in the design.

Requirements
Must have
• Gold foil accents

```html
<!DOCTYPE html>
<html lang="en">
<head>
<meta charset="utf-8">
<title>The Loom Briefing — Business Card</title>
<link rel="stylesheet" href="https://fonts.googleapis.com/css2?family=Montserrat:wght@700&family=Open+Sans:wght@400;600&display=swap">
<style>
  :root {
    --bg: #161616;
    --card: #242424;
    --gold: #e6bb48;
    --white: #ffffff;
    --muted: #e9e9e9;
  }
  * { margin: 0; padding: 0; box-sizing: border-box; }
  html, body { width: 1200px; height: 900px; overflow: hidden; background: var(--bg); }
  .sheet {
    width: 1200px; height: 900px;
    display: flex; flex-direction: column; align-items: center; justify-content: center;
    gap: 28px;
    font-family: "Open Sans", sans-serif;
  }
  .card {
    position: relative;
    width: 700px; height: 400px;
    background: var(--card);
    box-shadow: 0 10px 30px rgba(0,0,0,.55);
    overflow: hidden;
  }
  .card__band {
    position: absolute; left: 0; right: 0; bottom: 0;
    height: 10px; background: var(--gold);
  }
  .brand {
    display: flex; align-items: center; gap: 12px;
    color: var(--white);
    font-family: "Open Sans", sans-serif;
    font-weight: 600;
    letter-spacing: 1px;
  }
  .brand__dot {
    width: 14px; height: 14px; border-radius: 50%;
    background: var(--gold);
  }
  /* front */
  .card--front .brand {
    position: absolute; left: 0; right: 0; top: 130px;
    justify-content: center; font-size: 44px;
  }
  .tagline {
    position: absolute; left: 0; right: 0; top: 238px;
    text-align: center; color: var(--white);
    font-size: 17px; letter-spacing: .3px;
  }
  /* back */
  .card--back .brand {
    position: absolute; left: 60px; top: 70px; font-size: 32px;
  }
  .contact {
    position: absolute; left: 60px; top: 206px;
    list-style: none; color: var(--muted); font-size: 15px;
  }
  .contact__item { display: flex; align-items: center; gap: 10px; height: 28px; }
  .contact__icon { width: 16px; height: 16px; flex: none; }
  .person {
    position: absolute; right: 60px; top: 226px; text-align: right;
  }
  .person__name {
    font-family: "Montserrat", sans-serif; font-weight: 700;
    color: var(--gold); font-size: 24px; letter-spacing: 1px; text-transform: uppercase;
  }
  .person__title { color: var(--muted); font-size: 15px; margin-top: 2px; }
  .divider {
    position: absolute; left: 60px; right: 60px; top: 312px;
    height: 1px; background: var(--gold);
  }
</style>
</head>
<body>
<main class="sheet">
  <section class="card card--front" aria-label="Card front">
    <div class="brand"><span class="brand__dot"></span><span>The Loom Briefing</span></div>
    <p class="tagline">Corporate Workwear &amp; Uniform Specialist | Personal Stylist</p>
    <div class="card__band"></div>
  </section>

  <section class="card card--back" aria-label="Card back">
    <div class="brand"><span class="brand__dot"></span><span>The Loom Briefing</span></div>
    <ul class="contact">
      <li class="contact__item">
        <svg class="contact__icon" viewBox="0 0 16 16" aria-hidden="true"><path fill="#e6bb48" d="M3.5 1.5l2.3 2.6-1.2 1.7c.9 2 2.5 3.6 4.5 4.5l1.7-1.2 2.6 2.3-1.3 2.1C6.8 13.2 2.8 9.2 1.4 2.8z"/></svg>
        <span>+61 8 7142 5809</span>
      </li>
      <li class="contact__item">
        <svg class="contact__icon" viewBox="0 0 16 16" aria-hidden="true"><rect x="1" y="3.5" width="14" height="9" fill="#e6bb48"/><path d="M1.5 4l6.5 5 6.5-5" fill="none" stroke="#242424" stroke-width="1.2"/></svg>
        <span>belinda@theloombriefing.example</span>
      </li>
      <li class="contact__item">
        <svg class="contact__icon" viewBox="0 0 16 16" aria-hidden="true"><circle cx="8" cy="8" r="7" fill="#e6bb48"/><path d="M1 8h14M8 1c-3 3.5-3 10.5 0 14M8 1c3 3.5 3 10.5 0 14" fill="none" stroke="#242424" stroke-width="1"/></svg>
        <span>www.theloombriefing.example</span>
      </li>
    </ul>
    <div class="person">
      <p class="person__name">Belinda Harwick</p>
      <p class="person__title">Director and Stylist</p>
    </div>
    <div class="divider"></div>
    <div class="card__band"></div>
  </section>
</main>
</body>
</html>
```